TLK Electricial Contracting Services

Hi guys, after a design for my small electrical company, have logo design files to be incorporated into the layout, the basic concept is electrical contracting services for residential, commercial, industrial & data services, image is clean clear and strong,

Card format is to have a nice clean logo on front,with maybe the Residential – commercial – industrial - data, followed with licensed & insured, followed by contact details on backside of the card.

Target Market(s)

Residential, commercial, industrial sectors.

Industry/Entity Type

Electrical

Contact Information for Business Card

TLK logo,
Residential – commercial – industrial - data
REC: 61307
Email: tlk@vornamail.net.au
Phone: 0487 352 019

Requirements
Must have
• Clean & strong design.
Nice to have
• If possible, I would like the logo colours inverted so the text is orange and the background is black on the front of the card, then the backside of the card be the reverse colour
Should not have
• No Sparks, lightning bolts,

```html
<!DOCTYPE html>
<html lang="en">
<head>
<meta charset="UTF-8">
<title>TLK Electricial Contracting Services – Business Card</title>
<link rel="stylesheet" href="https://fonts.googleapis.com/css2?family=Open+Sans:wght@400;600;700&display=swap">
<style>
  :root {
    --backdrop: #8d8d8d;
    --card-black: #000000;
    --info-strip: #141414;
    --brand-orange: #f07f23;
    --paper-white: #ffffff;
    --text-light: #f2f2f2;
  }
  * { margin: 0; padding: 0; box-sizing: border-box; }
  html, body {
    width: 1200px;
    height: 900px;
    overflow: hidden;
    background: var(--backdrop);
    font-family: "Open Sans", Arial, sans-serif;
  }
  .canvas {
    width: 1200px;
    height: 900px;
    display: flex;
    flex-direction: column;
    align-items: center;
    justify-content: center;
    gap: 40px;
  }
  .card {
    position: relative;
    width: 630px;
    height: 360px;
    background: var(--card-black);
    overflow: hidden;
    box-shadow: 0 6px 18px rgba(0, 0, 0, 0.25);
  }

  /* shared bottom bands */
  .band { position: absolute; left: 0; width: 100%; }
  .band--white { background: var(--paper-white); }
  .band--orange { background: var(--brand-orange); }

  /* front side */
  .card-front .brand {
    position: absolute;
    left: 0;
    right: 0;
    top: 88px;
    text-align: center;
    color: var(--paper-white);
    font-weight: 700;
  }
  .brand-name {
    display: block;
    font-size: 98px;
    line-height: 1;
    letter-spacing: -1px;
  }
  .brand-tagline {
    display: block;
    font-size: 19px;
    letter-spacing: 0.5px;
    margin-top: 2px;
  }
  .card-front .band--white.top { top: 270px; height: 6px; }
  .card-front .band--orange.main { top: 276px; height: 84px; }

  /* back side */
  .card-back .brand {
    position: absolute;
    left: 48px;
    top: 34px;
    color: var(--brand-orange);
    font-weight: 700;
  }
  .card-back .brand-name { font-size: 84px; }
  .card-back .brand-tagline { font-size: 17px; }

  .holder {
    position: absolute;
    right: 48px;
    top: 58px;
    text-align: right;
  }
  .holder-name {
    color: var(--brand-orange);
    font-weight: 600;
    font-size: 20px;
    letter-spacing: 1px;
  }
  .holder-role {
    color: var(--text-light);
    font-size: 17px;
    margin-top: 2px;
  }

  .info-strip {
    position: absolute;
    left: 0;
    top: 168px;
    width: 100%;
    height: 108px;
    background: var(--info-strip);
  }
  .contact {
    position: absolute;
    color: var(--text-light);
    font-size: 15px;
    line-height: 24px;
  }
  .contact-line { display: flex; align-items: center; gap: 7px; white-space: nowrap; }
  .icon { width: 13px; height: 13px; flex: none; fill: var(--brand-orange); }
  .contact--sectors { left: 30px; top: 8px; }
  .contact--phones { left: 262px; top: 26px; }
  .contact--web { left: 418px; top: 44px; }

  .card-back .band--white.top { top: 276px; height: 6px; }
  .card-back .band--orange.main { top: 282px; height: 44px; }
  .card-back .band--white.mid { top: 326px; height: 4px; }
  .card-back .band--orange.base { top: 330px; height: 30px; }
</style>
</head>
<body>
<main class="canvas">

  <section class="card card-front" aria-label="Card front">
    <div class="brand">
      <span class="brand-name">TLK</span>
      <span class="brand-tagline">Tobin Lake Electrical</span>
    </div>
    <div class="band band--white top"></div>
    <div class="band band--orange main"></div>
  </section>

  <section class="card card-back" aria-label="Card back">
    <div class="brand">
      <span class="brand-name">TLK</span>
      <span class="brand-tagline">Tobin Lake Electrical</span>
    </div>

    <div class="holder">
      <p class="holder-name">DANIEL HARTLEY</p>
      <p class="holder-role">Managing Director</p>
    </div>

    <div class="info-strip">
      <div class="contact contact--sectors">
        <p class="contact-line">
          <svg class="icon" viewBox="0 0 12 12" aria-hidden="true"><path d="M6 0a4 4 0 0 0-4 4c0 3 4 8 4 8s4-5 4-8a4 4 0 0 0-4-4zm0 5.6A1.6 1.6 0 1 1 6 2.4a1.6 1.6 0 0 1 0 3.2z"/></svg>
          Residential – Commercial –
        </p>
        <p class="contact-line">Industrial – Data</p>
      </div>

      <div class="contact contact--phones">
        <p class="contact-line">
          <svg class="icon" viewBox="0 0 12 12" aria-hidden="true"><path d="M1 4c0-2 2-3 5-3s5 1 5 3v1H8.5V3.8h-5V5H1zM3 6h6l2 4H1z"/></svg>
          0487 352 019
        </p>
        <p class="contact-line">
          <svg class="icon" viewBox="0 0 12 12" aria-hidden="true"><path d="M1 1h10v10H1zm2 5.2l2.2 2.2L9.4 4.2 8.4 3.2 5.2 6.4 4 5.2z"/></svg>
          REC: 61307
        </p>
      </div>

      <div class="contact contact--web">
        <p class="contact-line">
          <svg class="icon" viewBox="0 0 12 12" aria-hidden="true"><path d="M0 2h12v1L6 7 0 3zm0 2.4l6 4 6-4V10H0z"/></svg>
          tlk@vornamail.net.au
        </p>
        <p class="contact-line">
          <svg class="icon" viewBox="0 0 12 12" aria-hidden="true"><path d="M4.5 7.5l3-3 1 1-3 3zM2 7l2-2 1 1-2 2a1 1 0 0 0 1 1l2-2 1 1-2 2a2.4 2.4 0 0 1-3.4-3.4zM10 5L8 7 7 6l2-2a1 1 0 0 0-1-1L6 5 5 4l2-2a2.4 2.4 0 0 1 3.4 3.4z"/></svg>
          Licensed &amp; Insured
        </p>
      </div>
    </div>

    <div class="band band--white top"></div>
    <div class="band band--orange main"></div>
    <div class="band band--white mid"></div>
    <div class="band band--orange base"></div>
  </section>

</main>
</body>
</html>
```